Commercial Waterproofing Modern Business Cards

We are a Commercial Waterproofing company. We do a variety of jobs on the exterior of buildings. We repel from the top or scaffold to reach the areas. Cut out and recaulk expansion joints and apply sealants, brick/concrete repairs, seal window frame perimeters, and much more. Our website is www.tallwallmend.com.
We are looking for a new business card design that would look more modern and cutting edge. We like the transparent paper and had thought about using our logo, but maybe pulling it apart to where the building part is kind of in the background. I have attached 2 different logos that we use regularly. We want the design to be a little funky, but professional at the same time. We really don't want the logo to be incorporated by itself, but you can use the logo and take out the buildings and just use the name or vice versa. Please don't just put the logo on the card and the words around that.

Target Market(s)

Property Managers/Building Maintenance

Industry/Entity Type

Business

Contact Information for Business Card

Dorian Vellstrom President
Office (555)418-2097
Mobile (555)604-7351

Font styles to use
Serif

Requirements
Must have
• Nice overall design, somehow pulling from the logo for the design
Nice to have
• Look artsy and modern with a nice quality paper
Should not have
• Too many words or distracting designs. The logo 'as is'

```html
<!DOCTYPE html>
<html lang="en">
<head>
<meta charset="utf-8">
<title>TallWall Mend – Business Card</title>
<link rel="stylesheet" href="https://fonts.googleapis.com/css2?family=Quicksand:wght@500;600;700&display=swap">
<style>
  :root {
    --backdrop: #2b2b2d;
    --card-light: #f2f2f3;
    --card-mid: #d6d6d8;
    --card-edge: #b9b9bc;
    --brand-blue: #2f5f9c;
    --brand-blue-deep: #24528d;
    --skyline-cream: #e6dcb0;
    --arc-line: rgba(255,255,255,0.55);
  }
  * { margin: 0; padding: 0; box-sizing: border-box; }
  html, body {
    width: 1200px; height: 800px; overflow: hidden;
    background: var(--backdrop);
    font-family: "Quicksand", sans-serif;
  }
  .card {
    position: absolute; left: 100px; top: 114px;
    width: 1000px; height: 572px;
    border-radius: 34px; overflow: hidden;
    background: radial-gradient(ellipse at 58% 48%, var(--card-light) 0%, var(--card-mid) 55%, var(--card-edge) 100%);
    color: var(--brand-blue);
  }
  .card-arcs { position: absolute; inset: 0; }
  .logo-art {
    position: absolute; left: 80px; top: 238px;
    width: 225px; height: 225px;
    background: linear-gradient(160deg, var(--brand-blue) 0%, var(--brand-blue-deep) 100%);
  }
  .logo-art::after {
    content: ""; position: absolute; left: 30px; right: 30px; top: 40px; bottom: 40px;
    background: var(--skyline-cream); opacity: 0.85; border-radius: 4px;
  }
  .brand-name {
    position: absolute; left: 330px; top: 322px;
    display: flex; align-items: center; gap: 14px;
    font-weight: 700; font-size: 32px; color: var(--brand-blue);
  }
  .brand-square { width: 24px; height: 24px; background: var(--brand-blue); }
  .divider {
    position: absolute; left: 636px; top: 110px;
    width: 2px; height: 280px; background: var(--brand-blue);
    transform: rotate(-8deg);
  }
  .person { position: absolute; right: 70px; top: 54px; text-align: right; }
  .person-name { font-weight: 700; font-size: 36px; letter-spacing: 0.5px; }
  .person-title { font-weight: 500; font-size: 28px; letter-spacing: 1.5px; margin-top: 4px; }
  .contacts {
    position: absolute; right: 36px; top: 280px;
    list-style: none; display: flex; flex-direction: column; align-items: flex-end; gap: 26px;
  }
  .contact { display: flex; align-items: center; gap: 18px; font-size: 33px; font-weight: 500; letter-spacing: 1.5px; }
  .contact-icon { width: 46px; height: 46px; flex: none; }
</style>
</head>
<body>
  <article class="card">
    <svg class="card-arcs" viewBox="0 0 1000 572" aria-hidden="true">
      <g fill="none" stroke="var(--arc-line)" stroke-width="2">
        <path d="M0 180 Q 500 60 1000 150"/>
        <path d="M560 0 Q 450 300 560 572"/>
        <path d="M120 572 Q 300 200 760 0"/>
        <path d="M400 572 Q 700 320 1000 360"/>
      </g>
    </svg>

    <div class="logo-art" role="img" aria-label="City skyline illustration in blue and cream"></div>
    <div class="brand-name"><span class="brand-square"></span>TallWall Mend</div>

    <div class="divider"></div>

    <header class="person">
      <h1 class="person-name">Dorian Vellstrom</h1>
      <p class="person-title">President</p>
    </header>

    <ul class="contacts">
      <li class="contact">(555)418-2097
        <svg class="contact-icon" viewBox="0 0 46 46" aria-label="Office phone">
          <polygon points="23,2 44,17 36,43 10,43 2,17" fill="var(--brand-blue)"/>
          <path d="M16 14 l5 -2 3 6 -3 2 q2 5 6 7 l2 -3 6 3 -2 5 q-10 1 -17 -18z" fill="#fff"/>
        </svg>
      </li>
      <li class="contact">(555)604-7351
        <svg class="contact-icon" viewBox="0 0 46 46" aria-label="Mobile phone">
          <polygon points="23,2 44,17 36,43 10,43 2,17" fill="var(--brand-blue)"/>
          <rect x="16" y="11" width="14" height="24" rx="2" fill="none" stroke="#fff" stroke-width="2.5"/>
          <circle cx="23" cy="31" r="1.5" fill="#fff"/>
        </svg>
      </li>
      <li class="contact">www.tallwallmend.com
        <svg class="contact-icon" viewBox="0 0 46 46" aria-label="Website">
          <polygon points="23,2 44,17 36,43 10,43 2,17" fill="var(--brand-blue)"/>
          <rect x="12" y="14" width="22" height="15" rx="1.5" fill="#fff"/>
          <rect x="20" y="29" width="6" height="4" fill="#fff"/>
          <rect x="16" y="33" width="14" height="2.5" fill="#fff"/>
        </svg>
      </li>
    </ul>
  </article>
</body>
</html>
```